Local fast-growing company in the service sector

We are looking for a modern business card design, which should also appear on our letterheads

Target Market(s)

Private and industrial sectors

Contact Information for Business Card

Vorname Name
Kellberger Str. 18
71299 Haldenbrunn
Tel.: 07146-839214-0
Name@agentur-kvtl.de

Colors
9d9d9d
919191
aaaaaa

Requirements
Must have
• The logo (file) in silver

```html
<!DOCTYPE html>
<html lang="de">
<head>
<meta charset="utf-8">
<title>KVTL Visitenkarte</title>
<link rel="stylesheet" href="https://fonts.googleapis.com/css2?family=Arimo:wght@400;700&display=swap">
<style>
  :root {
    --silver: #9d9d9d;
    --silver-mid: #919191;
    --silver-light: #aaaaaa;
    --ink: #555555;
    --ink-soft: #6a6a6a;
    --rule: #d4d4d4;
    --paper: #ffffff;
    --backdrop-top: #f4f4f4;
    --backdrop-bottom: #dcdcdc;
    --map-tone: #f0f0f0;
  }
  * { box-sizing: border-box; margin: 0; padding: 0; }
  html, body { width: 940px; height: 1200px; overflow: hidden; }
  body {
    font-family: "Arimo", Arial, sans-serif;
    background: radial-gradient(ellipse at 50% 35%, var(--backdrop-top) 0%, var(--backdrop-bottom) 100%);
    position: relative;
  }
  .card {
    position: absolute;
    left: 239px;
    width: 516px;
    height: 295px;
    background: var(--paper);
    box-shadow: 0 2px 8px rgba(0,0,0,0.18);
  }
  .card--front { top: 63px; }
  .card--back { top: 460px; }

  .brand {
    position: absolute;
    display: flex;
    align-items: center;
    gap: 10px;
    color: var(--silver);
    font-weight: 700;
  }
  .brand__mark {
    width: 38px; height: 38px;
    background: var(--silver-light);
  }
  .brand__name { font-size: 50px; line-height: 1; letter-spacing: 1px; }
  .card--front .brand { top: 48px; right: 18px; }

  .holder {
    position: absolute;
    left: 18px; top: 130px;
    width: 480px;
    font-size: 19px;
    font-weight: 700;
    color: var(--ink);
    padding-bottom: 5px;
    border-bottom: 1px solid var(--rule);
  }
  .contact {
    position: absolute;
    left: 258px; top: 178px;
    color: var(--ink-soft);
    font-size: 14px;
    line-height: 17px;
    font-style: normal;
  }
  .contact__company { font-weight: 700; color: var(--ink); font-size: 13px; }
  .contact__lines { margin-bottom: 6px; }
  .contact__row { display: flex; align-items: center; gap: 3px; }
  .contact__icon { width: 12px; height: 12px; flex: none; }

  .map-field {
    position: absolute;
    inset: 30px 40px;
    background: radial-gradient(ellipse at center, var(--map-tone) 0%, var(--paper) 75%);
  }
  .card--back .brand {
    top: 50%; left: 50%;
    transform: translate(-50%, -50%);
  }
  .card--back .brand__name { font-size: 56px; }
</style>
</head>
<body>
  <section class="card card--front">
    <div class="brand">
      <span class="brand__mark"></span>
      <span class="brand__name">KVTL</span>
    </div>
    <h1 class="holder">Vorname Name</h1>
    <address class="contact">
      <div class="contact__lines">
        <div class="contact__company">KVTL</div>
        <div>Kellberger Str. 18</div>
        <div>71299 Haldenbrunn</div>
      </div>
      <div class="contact__row">
        <svg class="contact__icon" viewBox="0 0 12 12" aria-hidden="true">
          <circle cx="6" cy="6" r="6" fill="#9d9d9d"/>
          <path d="M4 3.2l1 1.3-.6.7c.4.9 1 1.5 1.9 1.9l.7-.6 1.3 1-.5 1c-2.5-.3-4.2-2-4.5-4.5z" fill="#fff"/>
        </svg>
        <span>07146-839214-0</span>
      </div>
      <div class="contact__row">
        <svg class="contact__icon" viewBox="0 0 12 12" aria-hidden="true">
          <circle cx="6" cy="6" r="6" fill="#9d9d9d"/>
          <rect x="3" y="4" width="6" height="4.2" fill="#fff"/>
          <path d="M3 4l3 2.4L9 4" stroke="#9d9d9d" stroke-width="0.7" fill="none"/>
        </svg>
        <span>Name@agentur-kvtl.de</span>
      </div>
    </address>
  </section>

  <section class="card card--back">
    <div class="map-field" role="img" aria-label="Dezente gepunktete Weltkarte als Hintergrund"></div>
    <div class="brand">
      <span class="brand__mark"></span>
      <span class="brand__name">KVTL</span>
    </div>
  </section>
</body>
</html>
```